Create a memorable Stationary for Security Software Company

Velbrantix is the worldwide leader in securing the Internet. Making Internet communications and critical data secure, reliable and available everywhere has been and continues to be our ongoing vision. We are committed to staying focused on real customer needs and to developing new and innovative security solutions that redefine the security landscape.

Industry/Entity Type

Internet

Font styles to use
Serif
Sans Serif
Script

Colors
0792cd
33a6d7
85cae6

```html
<!DOCTYPE html>
<html lang="en">
<head>
<meta charset="utf-8">
<title>Velbrantix Business Card</title>
<link rel="stylesheet" href="https://fonts.googleapis.com/css2?family=Open+Sans:wght@400;600;700&display=swap">
<style>
  :root {
    --brand-deep: #0792cd;
    --brand-mid: #33a6d7;
    --brand-light: #85cae6;
    --paper: #ffffff;
    --ink: #2b2b2b;
    --backdrop: #ece8e2;
  }
  * { margin: 0; padding: 0; box-sizing: border-box; }
  html, body {
    width: 1200px;
    height: 1117px;
    overflow: hidden;
    background: var(--backdrop);
    font-family: "Open Sans", Arial, sans-serif;
  }
  .card {
    position: absolute;
    width: 819px;
    height: 469px;
    border-radius: 40px;
    overflow: hidden;
    box-shadow: 0 2px 6px rgba(0,0,0,0.18);
  }
  .card-front { left: 343px; top: 63px; background: var(--paper); }
  .card-back { left: 56px; top: 577px; background: var(--brand-light); border-radius: 24px; }

  .front-band { position: absolute; left: 0; top: 0; width: 819px; height: 469px; }

  .brand-mark {
    position: absolute;
    left: 0; right: 0;
    display: flex;
    flex-direction: column;
    align-items: center;
    gap: 14px;
  }
  .card-front .brand-mark { top: 40px; }
  .card-back .brand-mark { top: 70px; opacity: 0.75; }
  .brand-dot {
    width: 120px; height: 120px;
    border-radius: 50%;
    background: var(--brand-mid);
  }
  .brand-name {
    font-weight: 700;
    font-size: 46px;
    color: var(--brand-mid);
    letter-spacing: 0.01em;
  }

  .person {
    position: absolute;
    top: 260px; left: 0; right: 0;
    text-align: center;
    font-size: 29px;
    color: var(--ink);
  }
  .person-name { font-weight: 700; color: var(--brand-deep); }

  .contact {
    position: absolute;
    left: 0; right: 0;
    display: flex;
    justify-content: center;
    gap: 18px;
    font-size: 20px;
    color: var(--paper);
  }
  .contact-row-1 { top: 361px; }
  .contact-row-2 { top: 396px; }
  .contact-row-3 { top: 430px; }
  .contact-item { display: flex; align-items: center; gap: 7px; }
  .contact-item svg { width: 17px; height: 17px; fill: var(--paper); }

  .back-url {
    position: absolute;
    left: 0; right: 0; top: 365px;
    text-align: center;
    font-size: 27px;
    letter-spacing: 0.2em;
    color: var(--ink);
  }
</style>
</head>
<body>

<section class="card card-front">
  <svg class="front-band" viewBox="0 0 819 469" aria-hidden="true">
    <path d="M0 380 Q410 280 819 380" fill="none" stroke="var(--brand-mid)" stroke-width="5"/>
    <path d="M0 410 Q410 300 819 400 L819 469 L0 469 Z" fill="var(--brand-deep)"/>
  </svg>

  <div class="brand-mark">
    <span class="brand-dot"></span>
    <span class="brand-name">Velbrantix</span>
  </div>

  <p class="person"><span class="person-name">Your Name,</span> Title</p>

  <div class="contact contact-row-1">
    <span class="contact-item">
      <svg viewBox="0 0 24 24"><path d="M6.6 10.8a15 15 0 0 0 6.6 6.6l2.2-2.2a1 1 0 0 1 1-.25 11.4 11.4 0 0 0 3.6.57 1 1 0 0 1 1 1V20a1 1 0 0 1-1 1A17 17 0 0 1 3 4a1 1 0 0 1 1-1h3.5a1 1 0 0 1 1 1c0 1.25.2 2.45.57 3.57a1 1 0 0 1-.25 1z"/></svg>
      012-345-6789
    </span>
    <span class="contact-item">
      <svg viewBox="0 0 24 24"><path d="M8 1h8a2 2 0 0 1 2 2v18a2 2 0 0 1-2 2H8a2 2 0 0 1-2-2V3a2 2 0 0 1 2-2zm0 3v13h8V4zm4 15a1 1 0 1 0 0 2 1 1 0 0 0 0-2z"/></svg>
      012-345-6789
    </span>
  </div>

  <div class="contact contact-row-2">
    <span class="contact-item">
      <svg viewBox="0 0 24 24"><path d="M2 6a2 2 0 0 1 2-2h16a2 2 0 0 1 2 2v12a2 2 0 0 1-2 2H4a2 2 0 0 1-2-2zm2 .5V7l8 5 8-5v-.5z"/></svg>
      info@velbrantix.com
    </span>
    <span class="contact-item">
      <svg viewBox="0 0 24 24"><path d="M12 2a10 10 0 1 0 0 20 10 10 0 0 0 0-20zm6.9 9h-3a15 15 0 0 0-1.3-5.6A8 8 0 0 1 18.9 11zM12 4.1c.9 1.2 1.7 3.6 1.9 6.9h-3.8c.2-3.3 1-5.7 1.9-6.9zM9.4 5.4A15 15 0 0 0 8.1 11h-3a8 8 0 0 1 4.3-5.6zM5.1 13h3a15 15 0 0 0 1.3 5.6A8 8 0 0 1 5.1 13zm6.9 6.9c-.9-1.2-1.7-3.6-1.9-6.9h3.8c-.2 3.3-1 5.7-1.9 6.9zm2.6-1.3a15 15 0 0 0 1.3-5.6h3a8 8 0 0 1-4.3 5.6z"/></svg>
      www.velbrantix.com
    </span>
  </div>

  <div class="contact contact-row-3">
    <span class="contact-item">
      <svg viewBox="0 0 24 24"><path d="M12 2a7 7 0 0 0-7 7c0 5.2 7 13 7 13s7-7.8 7-13a7 7 0 0 0-7-7zm0 9.5A2.5 2.5 0 1 1 12 6.5a2.5 2.5 0 0 1 0 5z"/></svg>
      Street Name, City Name, Zipcode-012345
    </span>
  </div>
</section>

<section class="card card-back">
  <div class="brand-mark">
    <span class="brand-dot"></span>
    <span class="brand-name">Velbrantix</span>
  </div>
  <p class="back-url">www.velbrantix.com</p>
</section>

</body>
</html>
```